Honey Company from Florida Needs Sweet and Buzz-worthy Site

Website Requests:
-Deluxe 5-Page Website with SSL-Secure Online Store (Shopify)
-High-end imagery to appeal to a discerning consumer
-Detailed verbiage with strong SEO and easy readability
-Design principles: simple, chic, luxe, earthy
Pages:
1. Home {Local, Raw American Honey from Florida}
2. The Hive
> About Us
>Meet the Beekeepers
3. Buy Honey
> Shopify retail store
4. The Buzz {News, Recipes & More}
> Blog
5. Contact Us {We're Buzzin' to Meet You}
> Store Hours
> Phone Number
> Address
> Quick Contact Form
Attachments: Web design notes, Logo, Color Codes, Inspiration Photos
Target Market(s)
High-end honey consumer in the U.S.
Industry/Entity Type
Upscale honey enthusiasts; direct to consumer sales.
Coding
Coded - Design and coding required
Number of Pages Required
5+ page
Requirements
Must have
- Upscale look and feel, easy usability for quick sales.

```html
<!DOCTYPE html>
<html lang="en">
<head>
<meta charset="utf-8">
<title>Golden Comb Company — Raw Florida Honey</title>
<link rel="stylesheet" href="https://fonts.googleapis.com/css2?family=Spectral:wght@300;400;700&display=swap">
<style>
:root{
  --cream:#faf9ea;
  --honey:#e9d04f;
  --ink:#2a2a22;
  --text:#4b4a40;
  --rule:#c9c7b8;
  --field:#d6d4c4;
}
*{margin:0;padding:0;box-sizing:border-box}
html,body{width:1200px;height:4049px;overflow:hidden}
body{background:var(--cream);font-family:'Spectral',Georgia,serif;color:var(--text);position:relative;font-weight:300}
.abs{position:absolute}
.rule{position:absolute;left:111px;width:978px;height:1px;background:var(--rule)}
.notice{position:absolute;left:0;top:0;width:1200px;height:57px;background:var(--honey);color:var(--ink);font-size:16px;display:flex;align-items:center;justify-content:center;font-weight:400}
.search{left:108px;top:122px;display:flex;align-items:center;gap:14px}
.search span{font-size:15px;color:#8a887c;border-bottom:1px solid #8a887c;padding-bottom:2px;width:72px}
.brand{left:500px;top:90px;width:200px;display:flex;flex-direction:column;align-items:center;gap:10px}
.brand .dot{width:34px;height:34px;border-radius:50%;background:var(--honey)}
.brand .name{font-size:22px;font-weight:400;color:var(--ink);letter-spacing:1px}
.utility{left:1015px;top:122px;display:flex;gap:24px}
.nav{left:0;top:239px;width:1200px;display:flex;justify-content:center;gap:22px;font-size:17px;color:var(--ink);font-weight:400;letter-spacing:.2px}
.hero{left:111px;top:330px;width:978px;height:539px;background:linear-gradient(100deg,#3a2616 0%,#5b3d24 35%,#7a4d24 60%,#a05a1c 75%,#4a3220 100%)}
.hero-copy{left:234px;top:520px;color:#fff}
.hero-copy h1{font-size:25px;font-weight:700;letter-spacing:.5px}
.hero-copy p{font-size:20px;line-height:31px;margin-top:10px;width:390px;font-weight:300}
.play{left:235px;top:643px;width:59px;height:59px;border-radius:50%;background:#b99a2a;display:flex;align-items:center;justify-content:center}
.intro{left:111px;top:966px;width:978px;text-align:center}
.intro h2,.feature h2,.signup h2{font-weight:400;font-size:30px;color:var(--ink)}
.intro p{font-size:16px;line-height:30px;width:770px;margin:22px auto 0}
.intro a{display:inline-block;margin-top:14px;font-size:17px;font-weight:700;color:var(--ink);text-decoration:underline;text-underline-offset:4px}
.photo{position:absolute}
.feature h2{margin-bottom:18px}
.feature .quote{font-size:16px;margin-bottom:14px}
.feature p{font-size:16px;line-height:30px;margin-bottom:14px}
.btn{display:inline-flex;align-items:center;justify-content:center;background:var(--honey);color:var(--ink);font-size:15px;font-weight:400;width:144px;height:63px;border-radius:2px;text-transform:uppercase}
.signup{left:0;top:3535px;width:1200px;text-align:center}
.signup p{font-size:16px;margin-top:16px}
.signup form{display:flex;justify-content:center;gap:5px;margin-top:28px}
.field{width:290px;height:65px;border:1px solid var(--field);background:#fbfaf0;text-align:left;padding-left:24px;font-size:16px;display:flex;align-items:center;color:#555}
.foot-links{left:111px;top:3808px;display:flex;gap:22px;font-size:17px;color:var(--ink);font-weight:400}
.social{left:647px;top:3811px;display:flex;gap:26px}
.social i{width:16px;height:16px;border:2px solid var(--honey);border-radius:50%;display:block}
.contact{left:111px;font-size:16px;display:flex;gap:20px;color:var(--ink);font-weight:400}
.copy{left:111px;top:3982px;font-size:16px}
</style>
</head>
<body>
<div class="notice">Click to read our full COVID statement.</div>

<div class="abs search">
  <svg width="22" height="22" viewBox="0 0 22 22" fill="none" stroke="#333" stroke-width="1.8"><circle cx="9" cy="9" r="7"/><path d="M14 14l6 6"/></svg>
  <span>Search...</span>
</div>
<div class="abs brand"><div class="dot"></div><div class="name">GOLDEN COMB</div></div>
<div class="abs utility">
  <svg width="24" height="24" viewBox="0 0 24 24" fill="none" stroke="#333" stroke-width="1.6"><circle cx="12" cy="12" r="10"/><circle cx="12" cy="10" r="3.5"/><path d="M5.5 19c2-3 4-4 6.5-4s4.5 1 6.5 4"/></svg>
  <svg width="20" height="24" viewBox="0 0 20 24" fill="none" stroke="#333" stroke-width="1.6"><path d="M2 7h16l-1 15H3z"/><path d="M6.5 9V5a3.5 3.5 0 0 1 7 0v4"/></svg>
</div>
<nav class="abs nav"><span>HOME</span><span>THE HIVE</span><span>BUY HONEY</span><span>THE BUZZ</span><span>CONTACT</span></nav>
<div class="rule" style="top:289px"></div>

<div class="abs hero" role="img" aria-label="Honey dripping from a wooden dipper into a glass jar on a rustic table"></div>
<svg class="abs" style="left:155px;top:582px" width="20" height="36" viewBox="0 0 20 36" fill="none" stroke="#fff" stroke-width="2"><path d="M16 2L3 18l13 16"/></svg>
<svg class="abs" style="left:1029px;top:582px" width="20" height="36" viewBox="0 0 20 36" fill="none" stroke="#fff" stroke-width="2"><path d="M4 2l13 16L4 34"/></svg>
<div class="abs hero-copy"><h1>BLESSED TO BEE-KEEP</h1><p>Straight from our beloved hives to your lovely home</p></div>
<div class="abs play"><svg width="18" height="20" viewBox="0 0 18 20"><path d="M2 1l15 9-15 9z" fill="#fff"/></svg></div>

<div class="rule" style="top:911px"></div>
<section class="abs intro">
  <h2>Golden Comb Honey Farm</h2>
  <p>100% raw, unfiltered Florida honey straight from the beehives on his six-acre property, Golden Comb Honey Farm, 1840 Meadow Lane in Lakeview.<br>Agricultural Company specializing in the Production of 100% Raw American Honey, and the Pollination of America's food</p>
  <a>Read more</a>
</section>
<div class="rule" style="top:1261px"></div>

<div class="photo" style="left:649px;top:1340px;width:440px;height:572px;background:linear-gradient(160deg,#4a4a48,#3a3a38 60%,#2e2e2c)" role="img" aria-label="Honey jar with bee-patterned lid beside an open gift box"></div>
<section class="abs feature" style="left:111px;top:1440px;width:440px">
  <h2>Importance of bees</h2>
  <div class="quote">“Don't Judge a Bee by Its Stinger”</div>
  <p>If the bee disappeared off the face of the Earth, man would have only four years left to live.</p>
  <p>Hyper-efficient insects do play a vital role in agriculture. Almonds, for example, are almost entirely dependent on honeybee pollination.</p>
  <div class="btn" style="margin-top:8px">Read more</div>
</section>
<div class="rule" style="top:1990px"></div>

<div class="photo" style="left:111px;top:2069px;width:439px;height:571px;background:linear-gradient(135deg,#1e1e1c 0%,#2a2820 50%,#b8863e 100%)" role="img" aria-label="Black gift boxes with yellow lining holding honey jars"></div>
<section class="abs feature" style="left:669px;top:2191px;width:420px">
  <h2>The health benefits of honey</h2>
  <div class="quote">“Real Local Honey, Really Good for You”</div>
  <p>Raw honey is loaded with antioxidants to protect your body from cell damage due to free radicals. Honey has been long known as a folk remedy to help heal burns and wounds due to its antibacterial and antifungal properties.</p>
  <div class="btn" style="margin-top:8px">Read more</div>
</section>
<div class="rule" style="top:2727px"></div>

<div class="photo" style="left:111px;top:2813px;width:459px;height:573px;background:linear-gradient(180deg,#e8e4dc,#d4b47a 55%,#c9a260)" role="img" aria-label="Kraft gift box with three bottles of honey"></div>
<div class="photo" style="left:627px;top:2813px;width:460px;height:573px;background:linear-gradient(180deg,#e6e6e4,#c89a5c 50%,#7a4520)" role="img" aria-label="Hexagonal honey jars in kraft packaging"></div>
<div class="rule" style="top:3481px"></div>

<section class="abs signup">
  <h2>Sign-up for Our Emails</h2>
  <p>Sign up today to receive updates on new arrivals and exclusive deals.</p>
  <form><div class="field">Email address</div><div class="btn">Read more</div></form>
</section>
<div class="rule" style="top:3778px"></div>

<nav class="abs foot-links"><span>Home</span><span>The Hive</span><span>Buy Honey</span><span>The Buzz</span><span>Contact</span></nav>
<div class="abs social"><i></i><i></i></div>
<div class="abs contact" style="top:3847px">
  <svg width="20" height="20" viewBox="0 0 24 24"><path d="M6.6 10.8a15 15 0 0 0 6.6 6.6l2.2-2.2a1 1 0 0 1 1-.25 11.4 11.4 0 0 0 3.6.57 1 1 0 0 1 1 1V20a1 1 0 0 1-1 1A17 17 0 0 1 3 4a1 1 0 0 1 1-1h3.5a1 1 0 0 1 1 1c0 1.25.2 2.45.57 3.6a1 1 0 0 1-.25 1z" fill="var(--honey)"/></svg>
  <span>(352) 555-0148</span>
</div>
<div class="abs contact" style="top:3885px">
  <svg width="20" height="20" viewBox="0 0 24 24"><path d="M12 2a7 7 0 0 0-7 7c0 5 7 13 7 13s7-8 7-13a7 7 0 0 0-7-7zm0 9.5A2.5 2.5 0 1 1 12 6.5a2.5 2.5 0 0 1 0 5z" fill="var(--honey)"/></svg>
  <span style="line-height:30px;margin-top:-3px">1840 Meadow Lane,<br>Lakeview, FL 32000</span>
</div>
<div class="abs copy">© 2021 Golden Comb Company. All Rights Reserved</div>
</body>
</html>
```